Tech business card design

We need an amazing business card design for our new business 'Pexla' a marketing tech startup based in Sydney, Australia. We provide an online marketplace for businesses to search and buy advertising media, connect with service providers and learn more about marketing. We wish to communicate 'cool tech', reliability and professionalism and design based around our logo.

Target Market(s)

Business Owners

Contact Information for Business Card

Name
Position
Email Address
Website
Phone Number

Font styles to use
Other font styles liked:
• Avenir & Avenir Next

Colors

Designer to choose colors to be used in the design.

```html
<!DOCTYPE html>
<html lang="en">
<head>
<meta charset="utf-8">
<title>Pexla business card</title>
<link href="https://fonts.googleapis.com/css2?family=Nunito+Sans:ital,wght@0,400;0,700;0,800;0,900;1,700&display=swap" rel="stylesheet">
<style>
  :root {
    --navy: #1c1f52;
    --paper: #ffffff;
    --ink: #1c1f52;
    --rule: #3a3d66;
    --stage: #2b2b2f;
  }
  * { box-sizing: border-box; margin: 0; padding: 0; }
  html, body { width: 1200px; height: 800px; overflow: hidden; }
  body {
    background: var(--stage);
    font-family: "Nunito Sans", Arial, sans-serif;
    display: flex;
    align-items: center;
    justify-content: center;
    gap: 70px;
  }
  .card {
    width: 340px;
    height: 560px;
    position: relative;
    overflow: hidden;
    box-shadow: 0 14px 36px rgba(0,0,0,.45);
  }

  /* front */
  .card-front { background: var(--navy); }
  .front-wordmark {
    position: absolute;
    left: 34px; bottom: 54px;
    color: var(--paper);
    font-weight: 900;
    font-size: 86px;
    line-height: 1;
    letter-spacing: -1px;
  }

  /* back */
  .card-back { background: var(--paper); color: var(--ink); }
  .back-wordmark {
    position: absolute;
    top: 40px; left: 0; right: 0;
    text-align: center;
    font-weight: 900;
    font-size: 74px;
    line-height: 1;
    letter-spacing: -1px;
    color: var(--ink);
  }
  .contact {
    position: absolute;
    top: 150px; left: 60px; right: 60px;
    text-align: center;
    font-size: 15px;
    line-height: 1.25;
  }
  .person-name { font-weight: 800; font-size: 21px; }
  .person-role { font-size: 16px; }
  .rule { height: 1.5px; background: var(--rule); margin: 12px 0; }
  .label { font-weight: 700; font-style: italic; font-size: 13px; }
  .value { margin-bottom: 6px; }
  .social-row {
    display: flex; align-items: center; gap: 8px; margin-top: 14px;
  }
  .social-row .line { flex: 1; height: 1.5px; background: var(--rule); }
  .social-row svg { display: block; }
  .footer-band {
    position: absolute; left: 0; right: 0; bottom: 0; height: 66px;
  }
  .footer-band svg { position: absolute; inset: 0; width: 100%; height: 100%; }
  .website {
    position: absolute; left: 0; right: 0; bottom: 10px;
    text-align: center;
    color: var(--paper);
    font-size: 15px;
    letter-spacing: .5px;
  }
  .website b { font-weight: 800; }
</style>
</head>
<body>
  <div class="card card-front">
    <div class="front-wordmark">pexla</div>
  </div>

  <div class="card card-back">
    <div class="back-wordmark">pexla</div>
    <div class="contact">
      <div class="person-name">Liam Carter</div>
      <div class="person-role">Manager</div>
      <div class="rule"></div>
      <div class="label">Phone:</div>
      <div class="value">555.010.2468</div>
      <div class="label">Email:</div>
      <div class="value">info@pexlamail.com</div>
      <div class="rule"></div>
      <div class="address">PO BOX 480, your address<br>9th street Sydney<br>Australia</div>
      <div class="social-row">
        <span class="line"></span>
        <svg width="24" height="24" viewBox="0 0 24 24" aria-hidden="true"><circle cx="12" cy="12" r="11" fill="var(--navy)"/></svg>
        <svg width="24" height="24" viewBox="0 0 24 24" aria-hidden="true"><circle cx="12" cy="12" r="11" fill="var(--navy)"/></svg>
        <span class="line"></span>
      </div>
    </div>
    <div class="footer-band">
      <svg viewBox="0 0 340 66" preserveAspectRatio="none" aria-hidden="true">
        <path d="M0 0 H36 Q48 0 50 14 Q52 30 68 30 H272 Q288 30 290 14 Q292 0 304 0 H340 V66 H0 Z" fill="var(--navy)"/>
      </svg>
      <div class="website">www.<b>pexlaweb</b>.com</div>
    </div>
  </div>
</body>
</html>
```